Brindle Recycling needs a new web design

We need a new web design for our company based in Austin, TX. We resell and recycling electronics such as laptops, computer components, Zelvotabs, Quorns, etc. Since our inception over ten years ago, we’ve become one of the premier electronics recycling and remarketing companies in Austin, Texas.

```html
<!DOCTYPE html>
<html lang="en">
<head>
<meta charset="utf-8">
<title>Brindle Recycling</title>
<link href="https://fonts.googleapis.com/css2?family=Lato:wght@400;700&family=Open+Sans:wght@400;600&display=swap" rel="stylesheet">
<style>
:root{
  --navy:#0a2a66;
  --navy-deep:#061a44;
  --blue:#1a74d8;
  --blue-dark:#0d56b0;
  --accent:#1f6fc7;
  --ink:#222;
  --text:#555;
  --grey:#e6e6e6;
  --footer:#1e1e1e;
  --footer-bar:#141414;
  --white:#fff;
}
*{margin:0;padding:0;box-sizing:border-box}
html,body{width:1200px;height:2894px;overflow:hidden;background:var(--white)}
body{position:relative;font-family:"Open Sans",sans-serif;color:var(--text)}
.abs{position:absolute}
.header{left:0;top:0;width:1200px;height:97px;background:var(--white)}
.brand{left:112px;top:18px;display:flex;align-items:center;gap:12px}
.brand-dot{width:58px;height:58px;border-radius:50%;background:var(--navy)}
.brand-name{font-family:"Lato",sans-serif;font-weight:700;font-size:26px;color:var(--navy);line-height:1.05;width:150px}
.nav{right:118px;top:36px;display:flex;gap:30px;font-family:"Lato",sans-serif;font-size:18px;color:var(--ink)}
.nav a{color:inherit;text-decoration:none}
.nav a.active{color:var(--accent)}
.hero{left:0;top:97px;width:1200px;height:640px;background:radial-gradient(ellipse at 50% 40%,#1a4fa8 0%,var(--navy) 55%,var(--navy-deep) 100%)}
.hero-title{left:0;top:170px;width:1200px;text-align:center;font-family:"Lato",sans-serif;font-weight:700;font-size:40px;color:var(--white)}
.hero-sub{left:0;top:228px;width:1200px;text-align:center;font-family:"Lato",sans-serif;font-size:22px;color:#dbe6f7}
.btn{display:flex;align-items:center;justify-content:center;font-family:"Lato",sans-serif;font-weight:700;font-size:15px;letter-spacing:.5px;border-radius:4px}
.btn-hero{left:516px;top:270px;width:158px;height:45px;background:var(--white);color:var(--navy)}
.btn-outline{width:156px;height:48px;border:2px solid var(--accent);color:var(--navy);background:transparent}
.hero-media{left:395px;top:345px;width:395px;height:383px;background:linear-gradient(180deg,#8d97a6 0%,#6c7683 45%,#7cc23a 46%,#5da42a 100%);border-radius:10px}
.section-title{font-family:"Lato",sans-serif;font-weight:400;font-size:34px;color:var(--ink)}
.bio-title{left:137px;top:840px}
.bio-text{left:137px;top:900px;width:450px;font-size:16px;line-height:28px}
.bio-btn{left:137px;top:1069px}
.bio-video{left:622px;top:820px;width:457px;height:305px;background:linear-gradient(180deg,#51617a 0%,#8a8a82 50%,#6d6a62 100%)}
.play{left:818px;top:938px;width:68px;height:68px;border-radius:50%;background:var(--white)}
.about{left:0;top:1860px;width:1200px;height:565px;background:linear-gradient(90deg,#dcdcdc,#ececec)}
.capability{left:0;top:1225px;width:1200px;height:800px}
.cap-title{left:0;top:1292px;width:1200px;text-align:center;font-family:"Lato",sans-serif;font-weight:400;font-size:27px;color:var(--white)}
.cap-block{color:var(--white);text-align:center;font-family:"Lato",sans-serif;font-size:13px;line-height:24px}
.cap-block h3{font-family:"Lato",sans-serif;font-weight:400;font-size:25px;margin-bottom:6px}
.cap-center{left:505px;top:1538px;width:190px;height:190px;border-radius:50%;background:radial-gradient(circle,rgba(255,255,255,.22) 0%,rgba(255,255,255,.06) 70%,rgba(255,255,255,0) 100%)}
.about-photo{left:170px;top:2005px;width:335px;height:420px;background:linear-gradient(180deg,#d8d8d8 0%,#bfc3c8 50%,#eef0f2 100%)}
.about-title{left:540px;top:2065px;font-family:"Lato",sans-serif;font-weight:400;font-size:28px;color:var(--accent)}
.about-text{left:540px;top:2118px;width:470px;font-size:14.5px;line-height:25px;color:#6a6a6a}
.about-text p+p{margin-top:8px}
.about-btn{left:539px;top:2300px}
.footer{left:0;top:2425px;width:1200px;height:395px;background:var(--footer)}
.footer-bar{left:0;top:2820px;width:1200px;height:74px;background:var(--footer-bar);text-align:center;line-height:74px;font-size:13px;color:#888}
.f-brand{left:130px;top:2522px;display:flex;align-items:center;gap:12px}
.f-brand .brand-dot{width:62px;height:62px;background:var(--white)}
.f-brand .brand-name{color:var(--white);font-size:27px;width:180px}
.socials{left:142px;top:2622px;display:flex}
.social{width:44px;height:44px;border:2px solid var(--white);border-radius:50%;margin-right:2px}
.divider{width:1px;height:205px;background:#444;top:2505px}
.f-col h4{font-family:"Lato",sans-serif;font-weight:400;font-size:22px;color:var(--white);margin-bottom:18px}
.f-col li{list-style:none;font-size:13.5px;color:#ddd;line-height:31px}
.contact li{display:flex;align-items:flex-start;gap:10px;line-height:28px;font-size:13.5px}
.contact svg{margin-top:7px;flex:none}
</style>
</head>
<body>

<header class="abs header">
  <div class="abs brand"><span class="brand-dot"></span><span class="brand-name">Brindle Recycling</span></div>
  <nav class="abs nav">
    <a class="active" href="#">Home</a><a href="#">About Us</a><a href="#">Capabilities</a><a href="#">Our Services</a><a href="#">News</a><a href="#">Contact</a>
  </nav>
</header>

<section class="abs hero"></section>
<h1 class="abs hero-title">WE RESELL AND RECYCLING ELECTRONIC</h1>
<p class="abs hero-sub">Lorem ipsum dolor sit amet consectetuer adipiscing elit</p>
<a class="abs btn btn-hero">READ MORE</a>
<svg class="abs" style="left:0;top:600px" width="1200" height="140" viewBox="0 0 1200 140">
  <path d="M0 126 Q600 -40 1200 126" fill="none" stroke="#3d8cf0" stroke-width="10" opacity=".7"/>
  <path d="M0 126 Q600 -30 1200 126 L1200 140 L0 140 Z" fill="#fff"/>
</svg>
<div class="abs hero-media" role="img" aria-label="Green recycling bin filled with discarded electronics"></div>

<h2 class="abs section-title bio-title">COMPANY BIO</h2>
<p class="abs bio-text">What most people do not realize is electronic waste represents 2% of America's trash in landfills, but it equals 70% of overall toxic waste. Used computer equipment is a rapidly growing source of waste across the country. Only 12.5% of electronic waste is currently recycled in the US.</p>
<a class="abs btn btn-outline bio-btn">READ MORE</a>
<div class="abs bio-video" role="img" aria-label="Video still of a pile of old computer monitors"></div>
<div class="abs play"></div>
<svg class="abs" style="left:843px;top:956px" width="26" height="32"><path d="M2 2 L24 16 L2 30 Z" fill="#111"/></svg>

<section class="abs about"></section>

<svg class="abs capability" width="1200" height="800" viewBox="0 0 1200 800">
  <defs><linearGradient id="capBg" x1="0" y1="0" x2="1" y2="1"><stop offset="0" stop-color="#1c7ae0"/><stop offset="1" stop-color="#0b4fa8"/></linearGradient></defs>
  <path d="M0 0 H560 Q580 0 590 14 L598 22 Q600 24 602 22 L610 14 Q620 0 640 0 H1200 V676 C1000 760 800 790 600 757 C400 725 200 700 0 643 Z" fill="url(#capBg)"/>
  <path d="M590 8 L600 16 L610 8" fill="none" stroke="#9aa" stroke-width="2"/>
</svg>
<h2 class="abs cap-title">CAPABILITY OVERVIEW</h2>

<div class="abs cap-center" role="img" aria-label="Large recycling symbol at the centre of the capability wheel"></div>
<svg class="abs" style="left:420px;top:1460px" width="360" height="350" viewBox="0 0 360 350" fill="none" stroke="#fff" stroke-width="2">
  <line x1="180" y1="16" x2="180" y2="62"/><circle cx="180" cy="16" r="3.5" fill="#fff"/>
  <line x1="180" y1="284" x2="180" y2="330"/><circle cx="180" cy="284" r="3.5" fill="#fff"/>
  <line x1="12" y1="173" x2="55" y2="173"/><circle cx="12" cy="173" r="3.5" fill="#fff"/>
  <line x1="305" y1="173" x2="348" y2="173"/><circle cx="348" cy="173" r="3.5" fill="#fff"/>
</svg>

<div class="abs cap-block" style="left:440px;top:1360px;width:300px"><h3>Recycling</h3>Certified Global Recycling Capabilities<br>Sort by commodity<br>Certificate of Recycling</div>
<div class="abs cap-block" style="left:182px;top:1555px;width:280px"><h3>Logistics</h3>Global Logistics Support<br>Global Warehouse Capabilities<br>Global Audit Capabilities<br>Inventory Management<br>Asset Management<br>Bill of Lading</div>
<div class="abs cap-block" style="left:735px;top:1555px;width:300px"><h3>Certificates</h3>RC:2013 Responsible Recycling Certified<br>EMS 14100:2015<br>OHSP 18100:2007<br>State Board on Environmental<br>Stewardship (SBES)</div>
<div class="abs cap-block" style="left:440px;top:1800px;width:300px"><h3>Return</h3>Market Value Pricing<br>Profit Sharing</div>

<div class="abs about-photo" role="img" aria-label="Portrait of the company CEO in a white shirt, arms crossed"></div>
<h2 class="abs about-title">ABOUT DALE WHITFIELD</h2>
<div class="abs about-text">
  <p>As the CEO of Brindle Recycling, Dale Whitfield is responsible for running all facets of the business.Dale has a proven executive management track record and over 20 years of experience driving salesgrowth in the Recycling industry.</p>
  <p>Prior to founding Brindle Recycling in 2006, Dale was the Director of Sales for Halvern Trade Group Inc.</p>
</div>
<a class="abs btn btn-outline about-btn">READ MORE</a>

<footer class="abs footer"></footer>
<div class="abs f-brand"><span class="brand-dot"></span><span class="brand-name">Brindle Recycling</span></div>
<div class="abs socials" aria-label="Social links"><span class="social"></span><span class="social"></span><span class="social"></span><span class="social"></span></div>
<div class="abs divider" style="left:418px"></div>
<div class="abs divider" style="left:615px"></div>
<div class="abs divider" style="left:805px"></div>
<div class="abs f-col" style="left:460px;top:2505px"><h4>Quick Links</h4><ul><li>Home</li><li>Our Services</li><li>About Us</li><li>Capabilities</li></ul></div>
<div class="abs f-col" style="left:656px;top:2505px"><h4>Resources</h4><ul><li>Support</li><li>Dale Whitfield</li><li>Blogs</li><li>Contact Us</li></ul></div>
<div class="abs f-col contact" style="left:842px;top:2505px"><h4>Contact Us</h4>
  <ul>
    <li><svg width="14" height="18" viewBox="0 0 14 18"><path d="M7 0a7 7 0 0 0-7 7c0 5 7 11 7 11s7-6 7-11a7 7 0 0 0-7-7zm0 10a3 3 0 1 1 0-6 3 3 0 0 1 0 6z" fill="#fff"/></svg><span>2210 Larkspur Ridge Rd.<br>Austin, Texas 78799</span></li>
    <li><svg width="14" height="18" viewBox="0 0 14 18"><rect x="2" y="0" width="10" height="18" rx="2" fill="#fff"/><rect x="4" y="3" width="6" height="9" fill="#1e1e1e"/></svg><span>(512)555-0147 Cell</span></li>
    <li><svg width="16" height="16" viewBox="0 0 16 16"><rect x="3" y="0" width="10" height="5" fill="#fff"/><rect x="0" y="5" width="16" height="7" fill="#fff"/><rect x="3" y="10" width="10" height="6" fill="#fff" stroke="#1e1e1e"/></svg><span>(512)555-0192 Fax</span></li>
    <li><svg width="16" height="16" viewBox="0 0 16 16"><path d="M3 0l3 4-2 2c1 2 4 5 6 6l2-2 4 3-2 3C7 16 0 9 0 3z" fill="#fff"/></svg><span>(844)55-BRNDL (27635) Toll Free</span></li>
    <li><svg width="16" height="12" viewBox="0 0 16 12"><rect width="16" height="12" fill="#fff"/><path d="M0 0l8 7 8-7" fill="none" stroke="#1e1e1e" stroke-width="1.5"/></svg><span>Dale@BrindleRecycling.com</span></li>
  </ul>
</div>
<div class="abs footer-bar">© 2018 Company Name &nbsp;All right reserved</div>

</body>
</html>
```